Book Cover: Quiet Harbor: Small Ceremonies For The Restless Soul

I would like a full cover spread- front, back and spine as well as a stand alone front cover for Kindle for the book. Design a cover that mirrors the profound depth and dynamic energy of 'Quiet Harbor.' Envision a visual tapestry that draws readers into a transformative journey, where spirituality and self-care unite. Explore vibrant colors, intricate textures, and a sense of inner radiance that beckons readers to explore the book's rich wisdom within. See images for design inspiration attached. Even though some of the images are cartoon, I'd like the cover to be more serious than playful and very elegant.

About this book (back cover copy)
Are you ready to embark on a transformative journey and elevate your daily existence? "Quiet Harbor" is a treasure trove of practical yet profound rituals and wisdom from renowned self-care, healing, and spirituality experts.

Within these pages, you'll uncover a tapestry of guidance and insight from some of the world's most respected mentors. Their collective wisdom is your key to creating a sacred sanctuary within your everyday life.

From invigorating morning rituals to meditative practices, empowering affirmations, and transformative energy healing, you'll find a rich tapestry of tools to nurture a deeper connection with yourself and the universe.

Whether you're a seasoned practitioner or a newcomer to the world of self-care and spirituality, "Quiet Harbor" is your trusted companion on the journey to transform your life and elevate your daily experience. Open this book today and start your sacred, fulfilling adventure.

Colors
0094D4
00A9DD
6FCCEA
C7EBF8
E9F6FB
E54698
E96AAD
F1A4CE
F9D9EA
FCEFF6
6B429C
8869AF
B7A5CE
E3DAEB
F3F0F8

Requirements
Must have
• Title: Quiet Harbor: Subtitle: Small Ceremonies For The Restless Soul Name of Publisher: Lantern Bough Publishing- Logo on the back Back cover copy

```html
<!DOCTYPE html>
<html lang="en">
<head>
<meta charset="utf-8">
<title>Quiet Harbor – Cover Spread</title>
<link rel="stylesheet" href="https://fonts.googleapis.com/css2?family=Allison&family=Catamaran:wght@300;400;700&display=swap">
<style>
  :root{
    --stage:#1c1c1c;
    --paper:#fdf0f2;
    --blush:#f9dde4;
    --magenta:#d81466;
    --ink:#6e6e6e;
    --ink-dark:#2a2a2a;
    --swirl-a:#f2c94c;
    --swirl-b:#e96a3a;
    --swirl-c:#3aa6dd;
    --swirl-d:#6b429c;
  }
  *{box-sizing:border-box;margin:0;padding:0}
  html,body{width:1200px;height:1200px;overflow:hidden;background:var(--stage)}
  .spread{position:absolute;left:40px;top:203px;width:1120px;height:794px;background:var(--paper);overflow:hidden;font-family:"Catamaran",sans-serif;color:var(--ink)}
  .script{font-family:"Allison",cursive;color:var(--magenta);font-weight:400;line-height:1}

  /* back cover */
  .back{position:absolute;left:0;top:0;width:530px;height:794px}
  .back-title{position:absolute;left:0;width:530px;top:70px;text-align:center;font-size:118px}
  .back-subtitle{position:absolute;left:0;width:530px;top:172px;text-align:center;font-size:21px;font-weight:300}
  .blurb{position:absolute;left:50px;width:430px;top:212px;text-align:center;font-size:14.5px;line-height:21px;font-weight:300}
  .blurb p{margin-bottom:21px}
  .blurb .lead{color:var(--magenta);font-weight:400}
  .back-imprint{position:absolute;left:40px;top:700px;width:190px;text-align:center;font-size:22px;line-height:30px;color:var(--ink-dark);font-weight:400}
  .back-imprint .word{letter-spacing:2px}

  /* spine */
  .spine{position:absolute;left:530px;top:0;width:60px;height:794px}
  .spine-text{position:absolute;left:8px;top:40px;writing-mode:vertical-rl;white-space:nowrap;display:flex;align-items:center;gap:20px}
  .spine-title{font-size:56px}
  .spine-subtitle{font-size:16px;font-weight:300}
  .spine-imprint{font-size:16px;font-weight:400}
  .spine-imprint strong{font-weight:700}

  /* front cover */
  .front{position:absolute;left:590px;top:0;width:530px;height:794px}
  .cover-art{position:absolute;left:0;top:0}
  .front-subtitle{position:absolute;left:170px;top:70px;width:300px;text-align:center;font-size:29px;line-height:32px;font-weight:300}
  .front-title-1{position:absolute;left:20px;top:82px;font-size:230px}
  .front-title-2{position:absolute;left:95px;top:252px;font-size:170px}
  .front-imprint{position:absolute;left:37px;top:718px;font-size:25px;line-height:30px;font-weight:400;color:var(--ink)}
  .front-imprint strong{font-weight:700}
</style>
</head>
<body>
<div class="spread">

  <section class="back">
    <h2 class="script back-title">Quiet Harbor</h2>
    <p class="back-subtitle">Small Ceremonies For The Restless Soul</p>
    <div class="blurb">
      <p><span class="lead">Are you ready to embark on a transformative journey and elevate your daily existence?</span> <em>"Quiet Harbor"</em> is a treasure trove of practical yet profound rituals and wisdom from renowned self-care, healing, and spirituality experts.</p>
      <p>Within these pages, you'll uncover a tapestry of guidance and insight from some of the world's most respected mentors. Their collective wisdom is your key to creating a sacred sanctuary within your everyday life.</p>
      <p>From invigorating morning rituals to meditative practices, empowering affirmations, and transformative energy healing, you'll find a rich tapestry of tools to nurture a deeper connection with yourself and the universe.</p>
      <p>Whether you're a seasoned practitioner or a newcomer to the world of self-care and spirituality, "Quiet Harbor" is your trusted companion on the journey to transform your life and elevate your daily experience. Open this book today and start your sacred, fulfilling adventure.</p>
    </div>
    <p class="back-imprint">Lantern Bough<br><span class="word">Publishing</span></p>
  </section>

  <section class="spine">
    <div class="spine-text">
      <span class="script spine-title">Quiet Harbor</span>
      <span class="spine-subtitle">Small Ceremonies For The Restless Soul</span>
      <span class="spine-imprint"><strong>Lantern Bough</strong> Publishing</span>
    </div>
  </section>

  <section class="front">
    <svg class="cover-art" width="530" height="794" viewBox="0 0 530 794" role="img" aria-label="Cover artwork: a soft pink profile silhouette behind a vivid painted profile with flowing multicoloured hair">
      <defs>
        <linearGradient id="swirl" x1="0" y1="1" x2="1" y2="0">
          <stop offset="0" stop-color="var(--swirl-d)"/>
          <stop offset="0.3" stop-color="var(--swirl-b)"/>
          <stop offset="0.6" stop-color="var(--swirl-a)"/>
          <stop offset="1" stop-color="var(--swirl-c)"/>
        </linearGradient>
      </defs>
      <path d="M240 296 C320 300 420 300 530 300 L530 794 L170 794 C120 720 60 620 30 540 C60 450 140 320 240 296 Z" fill="var(--blush)"/>
      <path d="M530 290 C440 300 360 340 300 420 C250 470 220 560 200 640 C230 700 260 760 300 794 L530 794 Z" fill="url(#swirl)"/>
    </svg>
    <p class="front-subtitle">Small Ceremonies For<br>The Restless Soul</p>
    <h1 class="script front-title-1">Quiet</h1>
    <p class="script front-title-2">Harbor</p>
    <p class="front-imprint"><strong>Lantern Bough</strong><br>Publishing</p>
  </section>

</div>
</body>
</html>
```